NEW Modern Sleek Business Card for VR Language Startup

Our startup is using VR to lead the next wave of world language education. We need a two-sided business card that introduces the larger organization (Brightloom Language Inc) and our contact info on one side and shows the product, Glimwoorld, on the other side.

Side 1 (contact info)= Brightloom Logo and Contact info (name, title, phone, email)

Side 2 (product)= Glimworld logo, text, and website
Text= Culturally Immersive Language Learning Games
Website= www.glimworld-play.com

Target Market(s)

Education, Technology

Contact Information for Business Card

Contact info will be updated upon approval of the design. For now, put this as a placeholder.

Perry Dunmore
Founder & CEO
pdunmore@quillpost-mail.net
(555)-014-2286

Font styles to use
Other font styles liked:
• Gibson and Century Gothic are the brand fonts

Requirements
Nice to have
• I would love to see cohesion between the design and colors of the two logos. I have attached a few business card designs that I like, so you can get a feel for my preferred style.

```html
<!DOCTYPE html>
<html lang="en">
<head>
<meta charset="utf-8">
<title>Glimworld &amp; Brightloom Business Card</title>
<link rel="stylesheet" href="https://fonts.googleapis.com/css2?family=Questrial&family=Montserrat:wght@600;700&display=swap">
<style>
  :root {
    --page-bg: #e9e9ec;
    --card-bg: #ffffff;
    --ink: #1c1c1e;
    --ink-soft: #4a4a4d;
    --violet: #5b4cf5;
    --cyan: #1fd6e6;
    --accent-red: #e8323c;
    --card-shadow: 0 18px 40px rgba(0,0,0,0.18);
  }
  * { margin: 0; padding: 0; box-sizing: border-box; }
  html, body { width: 1200px; height: 1200px; overflow: hidden; }
  body {
    background: var(--page-bg);
    font-family: "Questrial", "Century Gothic", sans-serif;
    color: var(--ink);
    display: flex;
    flex-direction: column;
    align-items: center;
    justify-content: center;
    gap: 60px;
  }
  .card {
    width: 840px;
    height: 480px;
    background: var(--card-bg);
    border-radius: 36px;
    box-shadow: var(--card-shadow);
    position: relative;
    display: flex;
    flex-direction: column;
    align-items: center;
    justify-content: center;
  }

  /* Product side */
  .product-mark {
    display: flex;
    align-items: center;
    gap: 22px;
  }
  .product-dot {
    width: 120px;
    height: 120px;
    border-radius: 50%;
    background: linear-gradient(160deg, var(--cyan), var(--violet));
  }
  .product-name {
    font-size: 72px;
    color: var(--ink-soft);
    letter-spacing: 1px;
  }
  .product-tagline {
    margin-top: 14px;
    font-size: 24px;
    color: var(--ink-soft);
    letter-spacing: 0.5px;
  }
  .product-site {
    margin-top: 42px;
    font-family: "Montserrat", "Century Gothic", sans-serif;
    font-weight: 700;
    font-size: 22px;
    color: var(--violet);
  }

  /* Contact side */
  .contact-person {
    display: flex;
    align-items: baseline;
    gap: 14px;
    margin-bottom: 40px;
    margin-left: 120px;
  }
  .person-name {
    font-family: "Montserrat", "Century Gothic", sans-serif;
    font-weight: 700;
    font-size: 30px;
    letter-spacing: 0.5px;
    text-transform: uppercase;
  }
  .person-title { font-size: 21px; color: var(--ink-soft); }
  .company-mark {
    display: flex;
    align-items: center;
    gap: 32px;
  }
  .company-dot {
    width: 150px;
    height: 150px;
    border-radius: 50%;
    background: linear-gradient(200deg, #ff8a2a, var(--accent-red) 35%, var(--violet) 65%, var(--cyan));
  }
  .company-name {
    font-size: 76px;
    color: var(--ink);
    letter-spacing: 4px;
  }
  .contact-line {
    margin-top: 50px;
    display: flex;
    align-items: center;
    gap: 12px;
    font-size: 22px;
    color: var(--ink);
  }
  .contact-line svg { width: 22px; height: 22px; flex: none; }
  .contact-sep { margin: 0 6px; }
</style>
</head>
<body>

  <section class="card card--product">
    <div class="product-mark">
      <span class="product-dot" aria-hidden="true"></span>
      <span class="product-name">Glimworld</span>
    </div>
    <p class="product-tagline">Culturally Immersive Language Learning Games</p>
    <p class="product-site">www.glimworld-play.com</p>
  </section>

  <section class="card card--contact">
    <div class="contact-person">
      <span class="person-name">Perry Dunmore</span>
      <span class="person-title">Founder &amp; CEO</span>
    </div>
    <div class="company-mark">
      <span class="company-dot" aria-hidden="true"></span>
      <span class="company-name">Brightloom</span>
    </div>
    <div class="contact-line">
      <svg viewBox="0 0 24 24" aria-hidden="true">
        <rect x="2" y="5" width="20" height="14" rx="2" fill="var(--accent-red)"/>
        <path d="M3 6 L12 13 L21 6" fill="none" stroke="#fff" stroke-width="1.8"/>
      </svg>
      <span>pdunmore@quillpost-mail.net</span>
      <span class="contact-sep">|</span>
      <svg viewBox="0 0 24 24" aria-hidden="true">
        <path d="M6.6 10.8a15.1 15.1 0 0 0 6.6 6.6l2.2-2.2a1 1 0 0 1 1-.25 11.4 11.4 0 0 0 3.6.57 1 1 0 0 1 1 1V20a1 1 0 0 1-1 1A17 17 0 0 1 3 4a1 1 0 0 1 1-1h3.5a1 1 0 0 1 1 1c0 1.25.2 2.45.57 3.57a1 1 0 0 1-.25 1z" fill="var(--accent-red)"/>
      </svg>
      <span>(555)-014-2286</span>
    </div>
  </section>

</body>
</html>
```